Pinecrest Ridge Institute-Larkfield Kickoff Days

I am the Student Activities Coordinator at Pinecrest Ridge Institute-Larkfield. For Kickoff Days 2013, I need a standard poster 24x36 with the list of events happening. Our theme is based on the popular Tuesday Late Revue video "We're on a raft"
http://www.clipvaultexample.com/watch?v=Q4mzTpXwKa
Our theme is:
We're at the 'Field!
Kickoff Days 2013
Graphics on the poster should reflect popular images/designs of TLR We're on a raft. However, the boat should be a steamboat instead of the yacht image.
Unfortunately, I have a lot of text to fit on the poster. Traditionally we go with 3 margins listing events. I'm attaching the word document of events and our logo to this proposal. I'll also attach a few google images of "We're on a raft" that align with the type of theme I'm looking for.
One last thing, our logo contains mountains listing all of the different campuses. Remove the campus names and mountains all together. Use simply the Colorado flag C and "Pinecrest Ridge Institute".
Thanks for considering this brief!
Gavin
Target Market(s)
Our college students love to ski and snowboard. In fact, one of our degrees is "Alpine Slope Trade Studies". Their ages are 18-22.
Industry/Entity Type
Events
Look and feel

```html
<!DOCTYPE html>
<html lang="en">
<head>
<meta charset="utf-8">
<title>Pinecrest Ridge Institute – Kickoff Days 2013</title>
<link href="https://fonts.googleapis.com/css2?family=Anton&family=Open+Sans:wght@400;700&display=swap" rel="stylesheet">
<style>
  :root {
    --navy: #1f2d5e;
    --red: #bf3a47;
    --gold: #f5e43a;
    --white: #ffffff;
    --sky-top: #ffffff;
    --sky-bottom: #bfe9f7;
    --backdrop: #e9e6e1;
  }
  * { box-sizing: border-box; margin: 0; padding: 0; }
  html, body { width: 826px; height: 1200px; overflow: hidden; background: var(--backdrop); }
  .poster {
    position: absolute; left: 57px; top: 67px; width: 716px; height: 1073px;
    background: linear-gradient(180deg, var(--sky-top) 35%, var(--sky-bottom) 100%);
    overflow: hidden;
    font-family: "Open Sans", sans-serif;
  }
  .header-red { position: absolute; left: 238px; top: 0; width: 478px; height: 365px; background: var(--red); }
  .header-navy { position: absolute; left: 0; top: 0; width: 238px; height: 158px; background: var(--navy); }
  .brand {
    position: absolute; left: 30px; top: 66px; width: 190px;
    color: var(--white); font-family: "Open Sans", sans-serif; font-weight: 700;
    font-size: 15px; line-height: 20px;
  }
  .title {
    position: absolute; left: 318px; top: 30px; width: 380px; text-align: center;
    font-family: "Anton", sans-serif; color: var(--white); font-size: 37px; line-height: 1.12; font-weight: 400;
    text-shadow: -2px -2px 0 var(--navy), 2px -2px 0 var(--navy), -2px 2px 0 var(--navy), 2px 2px 0 var(--navy), 3px 3px 0 var(--navy);
  }
  .title .year { font-size: 50px; }
  .photo-sea {
    position: absolute; left: 0; top: 158px; width: 238px; height: 207px;
    background: linear-gradient(180deg, #cfe6f7 0%, #8fc0e6 35%, #1f63a8 55%, #0d3f80 100%);
  }
  .photo-steamboat {
    position: absolute; left: 405px; top: 160px; width: 285px; height: 160px; border-radius: 50%;
    background: radial-gradient(ellipse at center, #f4f1ec 0%, #ddd6cc 55%, #f1efe9 100%);
  }
  .photo-group {
    position: absolute; left: 445px; top: 853px; width: 258px; height: 215px;
    background: linear-gradient(180deg, rgba(120,120,130,0) 0%, rgba(90,95,110,.55) 40%, rgba(40,45,70,.7) 100%);
    border-radius: 110px 110px 8px 8px;
  }
  .day-card {
    position: absolute; background: var(--navy); border: 3px solid var(--white); border-radius: 6px;
    padding: 12px 12px 8px 13px; color: var(--white); font-size: 9.6px; line-height: 13px;
  }
  .day-title { font-family: "Anton", sans-serif; color: var(--gold); font-size: 14.5px; line-height: 18px; font-weight: 400; letter-spacing: .1px; margin-bottom: 3px; }
  .event { margin-top: 11px; }
  .day-title + .event { margin-top: 0; }
  .event + .day-title { margin-top: 18px; }
  .event-name { color: var(--gold); font-weight: 700; font-size: 10px; }
  .card-thu22 { left: 28px; top: 368px; width: 204px; height: 309px; }
  .card-sat24 { left: 240px; top: 368px; width: 204px; height: 309px; }
  .card-mon26 { left: 452px; top: 368px; width: 206px; height: 309px; }
  .card-fri23 { left: 28px; top: 686px; width: 204px; height: 356px; }
  .card-sun25 { left: 240px; top: 686px; width: 172px; height: 290px; }
  .card-thu29 { left: 420px; top: 686px; width: 162px; height: 211px; }
  .free-note {
    position: absolute; left: 252px; top: 996px; z-index: 2; color: var(--navy);
    font-weight: 700; font-size: 13px; line-height: 22px; letter-spacing: .1px;
  }
</style>
</head>
<body>
<main class="poster">
  <div class="header-red"></div>
  <div class="header-navy"></div>
  <div class="brand">Pinecrest Ridge Institute</div>
  <h1 class="title">We're at the 'Field!<br>Kickoff Days <span class="year">2013</span></h1>
  <div class="photo-sea" role="img" aria-label="Photo of a white yacht on open blue water"></div>
  <div class="photo-steamboat" role="img" aria-label="Photo of a white paddle-wheel steamboat"></div>

  <section class="day-card card-thu22">
    <h2 class="day-title">Thursday August 22</h2>
    <div class="event"><div class="event-name">Residence Hall Move-In</div>12:00pm-3:00pm<br>Hill Hall</div>
    <div class="event"><div class="event-name">Brunch</div>10:00am-1:00pm<br>Dining Hall</div>
    <div class="event"><div class="event-name">International Students Orientation</div>3:00pm<br>Hawthorn 121</div>
    <div class="event"><div class="event-name">Dinner</div>5:00pm-6:30pm<br>Dining Hall<br>Hot Springs Waterslide Party<br>7:00pm-9:00pm<br>Depot Street Hot Springs</div>
  </section>

  <section class="day-card card-sat24">
    <h2 class="day-title">Saturday August 24</h2>
    <div class="event"><div class="event-name">Main Street Farmers Market</div>9:00am-2:00pm<br>6th &amp; Lincoln (walking dist.)</div>
    <div class="event"><div class="event-name">Brunch</div>10:00am-1:00pm<br>Dining Hall</div>
    <div class="event"><div class="event-name">Bramblewood Hot Springs</div>2:00pm-5:00pm<br>Shuttle leaves Hill Hall at 1:30pm</div>
    <div class="event"><div class="event-name">Dinner</div>5:00-6:00pm<br>Dining Hall</div>
    <div class="event"><div class="event-name">Free Movie on the Mountain:<br>The Ember Trials</div>8:00pm<br>(LRT Buses to Resort,<br>5:35pm Last Bus)</div>
  </section>

  <section class="day-card card-mon26">
    <h2 class="day-title">Monday August 26</h2>
    <div class="event"><div class="event-name">Regular Dining Hall Hours Begin</div><div style="margin-top:6px">“Being Alone Sucks!”</div>9:00pm<br>Auditorium</div>
    <h2 class="day-title">Tuesday August 27</h2>
    <div class="event"><div class="event-name">Newly Roommate Game</div>7:00pm-8:00pm<br>Hill Hall: MPR</div>
    <div class="event"><div class="event-name">Free Gelato</div>8:00pm-9:00pm<br>Nonna Gelato 7th and Juniper</div>
    <h2 class="day-title">Wednesday August 28</h2>
    <div class="event"><div class="event-name">Free Bowling</div>9:00pm<br>Summit Lanes</div>
  </section>

  <section class="day-card card-fri23">
    <h2 class="day-title">Friday August 23</h2>
    <div class="event"><div class="event-name">Breakfast</div>7:30am-9:00am<br>Dining Hall</div>
    <div class="event"><div class="event-name">Hike Cedar Run Falls</div>9:00am-11:30am<br>Shuttle leaves Hill Hall at 8:30am</div>
    <div class="event"><div class="event-name">BBQ and Faculty Ice Cream Social</div>12:00pm-1:30pm<br>Dining Hall</div>
    <div class="event"><div class="event-name">Kick Off Party: Inflatables</div>1:30pm-4:00pm<br>Upper Parking Lot</div>
    <div class="event"><div class="event-name">Dinner</div>5:00pm-6:00pm<br>Dining Hall</div>
    <div class="event"><div class="event-name">Free Concert</div>7:00pm<br>Larkfield Ridge Base<br>(LRT Buses to Resort,<br>5:35pm Last Bus)</div>
  </section>

  <section class="day-card card-sun25">
    <h2 class="day-title">Sunday August 25</h2>
    <div class="event"><div class="event-name">Brunch</div>10:00am-1:00pm<br>Dining Hall</div>
    <div class="event"><div class="event-name">Alpine Slide/Volleyball</div>2:00pm-4:00pm<br>Meet at Thistle Hill</div>
    <div class="event"><div class="event-name">Dinner</div>5:00pm-6:00pm<br>Dining Hall</div>
    <div class="event"><div class="event-name">Mandatory All Hall Meeting</div>6:00pm<br>Auditorium</div>
    <div class="event"><div class="event-name">RHA Super Sunday Program</div>8:00pm<br>Hill Hall: MPR</div>
  </section>

  <section class="day-card card-thu29">
    <h2 class="day-title">Thursday August 29</h2>
    <div class="event"><div class="event-name">Club Fair</div>10:00am-2:00pm<br>Dining Hall</div>
    <div class="event"><div class="event-name">Black Light Dodgeball</div>9:00pm<br>Gym</div>
    <h2 class="day-title">Friday August 30</h2>
    <div class="event"><div class="event-name">Late Night Climbing</div>9:00pm<br>Gym</div>
  </section>

  <div class="photo-group" role="img" aria-label="Photo of a group of students gathered around a round picture of a boat"></div>
  <p class="free-note">ALL EVENTS ARE FREE<br>UNLESS OTHERWISE NOTED</p>
</main>
</body>
</html>
```